Harborline Auto LLC

Car Dealer Customer Service
Address: 2874 Cresthaven Road, Shelbyville, TN 37162
web: www.harborlineautoxq.net
email: harborlineautoxq@mailnest.example
Phone: (931) 555-0148
Phone: (629) 555-0173

```html
<!DOCTYPE html>
<html lang="en">
<head>
<meta charset="utf-8">
<title>Harborline Auto – Business Card</title>
<link rel="stylesheet" href="https://fonts.googleapis.com/css2?family=Lexend:wght@600&family=Poppins:ital,wght@0,400;0,600;1,400&display=swap">
<style>
  :root {
    --backdrop: #2b2b2b;
    --card-blue-light: #1f7db2;
    --card-blue-dark: #145d88;
    --text-white: #ffffff;
    --ring-white: #eef1f3;
    --accent-gold: #e2a93b;
  }
  * { margin: 0; padding: 0; box-sizing: border-box; }
  html, body {
    width: 1200px; height: 576px; overflow: hidden;
    background: var(--backdrop);
  }
  .canvas { position: relative; width: 1200px; height: 576px; }
  .card {
    position: absolute; top: 138px; height: 292px;
    border-radius: 9px; overflow: hidden;
    background: linear-gradient(160deg, var(--card-blue-light) 0%, var(--card-blue-dark) 100%);
    color: var(--text-white);
    font-family: "Poppins", sans-serif;
  }
  .card-front { left: 102px; width: 485px; }
  .card-back { left: 596px; width: 480px; }
  .brand-mark { position: absolute; width: 288px; height: 288px; top: 2px; }
  .card-front .brand-mark { left: 346px; }
  .card-back .brand-mark { left: -148px; }
  .brand-name {
    font-family: "Lexend", sans-serif; font-weight: 600;
    font-size: 28px; letter-spacing: 0.5px; text-transform: uppercase;
    color: var(--text-white); position: absolute; white-space: nowrap;
  }
  .card-front .brand-name { left: 26px; top: 32px; }
  .card-back .brand-name { right: 26px; top: 224px; color: var(--ring-white); }
  .role {
    position: absolute; left: 26px; top: 105px;
    font-style: italic; font-size: 13.5px;
  }
  .phones { position: absolute; left: 26px; top: 126px; list-style: none; }
  .phones li {
    display: flex; align-items: center; gap: 9px;
    font-weight: 600; font-size: 17.5px; line-height: 23px;
  }
  .contacts { position: absolute; left: 26px; top: 210px; list-style: none; font-size: 13px; line-height: 20px; }
  .contacts li { display: flex; align-items: center; gap: 9px; }
  .contacts .address { margin-top: 1px; }
  .icon { flex: none; fill: var(--accent-gold); }
</style>
</head>
<body>
<main class="canvas">
  <section class="card card-front" aria-label="Card front">
    <svg class="brand-mark" viewBox="0 0 288 288" aria-hidden="true">
      <circle cx="144" cy="144" r="128" fill="none" stroke="var(--ring-white)" stroke-width="30"/>
    </svg>
    <h1 class="brand-name">Harborline Auto</h1>
    <p class="role">Car Dealer Customer Service</p>
    <ul class="phones">
      <li><svg class="icon" width="16" height="13" viewBox="0 0 16 13"><path d="M1 4c0-2 3-3 7-3s7 1 7 3v1h-3V4H4v1H1z M3 6h10l1 6H2z"/></svg>(931) 555-0148</li>
      <li><svg class="icon" width="16" height="13" viewBox="0 0 16 13"><path d="M1 4c0-2 3-3 7-3s7 1 7 3v1h-3V4H4v1H1z M3 6h10l1 6H2z"/></svg>(629) 555-0173</li>
    </ul>
    <ul class="contacts">
      <li><svg class="icon" width="12" height="9" viewBox="0 0 12 9"><path d="M0 0h12v9H0z M1 1l5 4 5-4" fill="var(--accent-gold)"/></svg>www.harborlineautoxq.net</li>
      <li><svg class="icon" width="12" height="12" viewBox="0 0 12 12"><circle cx="6" cy="6" r="5.5"/></svg>harborlineautoxq@mailnest.example</li>
      <li class="address">2874 Cresthaven Road, Shelbyville, TN 37162</li>
    </ul>
  </section>
  <section class="card card-back" aria-label="Card back">
    <svg class="brand-mark" viewBox="0 0 288 288" aria-hidden="true">
      <circle cx="144" cy="144" r="128" fill="none" stroke="var(--ring-white)" stroke-width="30"/>
    </svg>
    <p class="brand-name">Harborline Auto</p>
  </section>
</main>
</body>
</html>
```